BRIGHT RIVER POWER.

I'd like my business logo.
contact name: Dennis Halvorsen
phone:0438759164
email: info@brightriverpower.net.au
website: www.brightriverpower.net.au

services:
solar
battery storage
LED lighting
energy saving solutions
general electrical
I'd like the design to look professional

Target Market(s)

Everyone

Industry/Entity Type

Business

Contact Information for Business Card

as described above

Requirements
Must have
• Id like the colours and the design to work well with my logo.

```html
<!DOCTYPE html>
<html lang="en">
<head>
<meta charset="utf-8">
<title>Bright River Power – Business Card</title>
<link rel="stylesheet" href="https://fonts.googleapis.com/css2?family=Source+Sans+3:wght@400;600;700&display=swap">
<style>
  :root {
    --backdrop: #3d3d3d;
    --card-white: #ffffff;
    --brand-green: #4fa637;
    --brand-orange: #f5a41f;
    --text-grey: #555555;
    --divider: #cfcfcf;
    --back-light: #8dc63f;
    --back-dark: #3f9c2e;
    --on-green: #ffffff;
  }
  * { margin: 0; padding: 0; box-sizing: border-box; }
  html, body {
    width: 1105px; height: 1200px; overflow: hidden;
    background: var(--backdrop);
    font-family: "Source Sans 3", "Myriad Pro", sans-serif;
  }
  .card {
    position: absolute; left: 193px; width: 720px; height: 410px;
  }
  .card-front { top: 167px; background: var(--card-white); }
  .card-back {
    top: 623px;
    background: radial-gradient(ellipse at 50% 45%, var(--back-light) 0%, #6ab536 45%, var(--back-dark) 100%);
  }

  /* Front */
  .brand-lockup {
    position: absolute; left: 0; right: 0; top: 120px;
    display: flex; align-items: center; justify-content: center; gap: 14px;
  }
  .brand-dot {
    width: 30px; height: 30px; border-radius: 50%;
    background: var(--brand-orange);
  }
  .brand-name {
    font-weight: 700; font-size: 40px; letter-spacing: 1px;
    color: var(--brand-green); line-height: 1;
  }
  .contact-name {
    position: absolute; right: 432px; top: 274px;
    font-size: 27px; font-weight: 600; color: var(--brand-green);
    text-align: right; white-space: nowrap; line-height: 1.2;
  }
  .contact-divider {
    position: absolute; left: 309px; top: 254px;
    width: 1px; height: 76px; background: var(--divider);
  }
  .contact-list {
    position: absolute; left: 335px; top: 250px;
    list-style: none;
  }
  .contact-item {
    display: flex; align-items: center; gap: 10px;
    height: 27.5px; font-size: 19px; color: var(--text-grey);
  }
  .contact-icon { width: 17px; height: 17px; flex: none; }

  /* Back */
  .back-lockup {
    position: absolute; left: 0; right: 0; top: 164px;
    display: flex; align-items: center; justify-content: center; gap: 14px;
  }
  .back-lockup .brand-dot { background: var(--on-green); }
  .back-lockup .brand-name { color: var(--on-green); }
  .service-list {
    position: absolute; left: 0; right: 0; top: 325px;
    text-align: center; color: var(--on-green);
    font-size: 20px; line-height: 26px;
  }
  .service-sep { display: inline-block; margin: 0 6px; font-size: 14px; vertical-align: 2px; }
</style>
</head>
<body>

<section class="card card-front">
  <div class="brand-lockup">
    <span class="brand-dot"></span>
    <span class="brand-name">BRIGHT RIVER POWER</span>
  </div>

  <p class="contact-name">Dennis Halvorsen</p>
  <span class="contact-divider"></span>

  <ul class="contact-list">
    <li class="contact-item">
      <svg class="contact-icon" viewBox="0 0 24 24" aria-hidden="true">
        <path fill="#4fa637" d="M6.6 10.8a15.1 15.1 0 0 0 6.6 6.6l2.2-2.2a1 1 0 0 1 1-.25 11.4 11.4 0 0 0 3.6.57 1 1 0 0 1 1 1V20a1 1 0 0 1-1 1A17 17 0 0 1 3 4a1 1 0 0 1 1-1h3.5a1 1 0 0 1 1 1c0 1.25.2 2.45.57 3.6a1 1 0 0 1-.25 1z"/>
      </svg>
      <span>0438759164</span>
    </li>
    <li class="contact-item">
      <svg class="contact-icon" viewBox="0 0 24 24" aria-hidden="true">
        <rect x="2" y="5" width="20" height="14" rx="1.5" fill="#4fa637"/>
        <path d="M3 6.5l9 6.5 9-6.5" fill="none" stroke="#fff" stroke-width="1.6"/>
      </svg>
      <span>info@brightriverpower.net.au</span>
    </li>
    <li class="contact-item">
      <svg class="contact-icon" viewBox="0 0 24 24" aria-hidden="true">
        <circle cx="12" cy="12" r="10" fill="#4fa637"/>
        <path d="M2 12h20M12 2c3 3 3 17 0 20M12 2c-3 3-3 17 0 20" fill="none" stroke="#fff" stroke-width="1.4"/>
      </svg>
      <span>brightriverpower.net.au</span>
    </li>
  </ul>
</section>

<section class="card card-back">
  <div class="back-lockup">
    <span class="brand-dot"></span>
    <span class="brand-name">BRIGHT RIVER POWER</span>
  </div>
  <p class="service-list">
    Solar<span class="service-sep">●</span>Battery storage<span class="service-sep">●</span>LED lighting<br>
    Energy saving solutions
  </p>
</section>

</body>
</html>
```